Home Page PSD Website Design - 1 Page *

Design an eye-catching home page design for a rubbish removal website.

Please review the document provided it contains all the details and there is a second document with all the content for the page that needs to be included.

Target Market(s)

Home owners, businesses, property managers, real estate agents

Industry/Entity Type

Waste Management

Number of Pages Required

1 page

Requirements
Must have
• Please review the document provided it contains all the details and there is a second document with all the content for the page that needs to be included.

PSD must be layered, all elements labeled and separated for easy coding.
Nice to have

```html
<!DOCTYPE html>
<html lang="en">
<head>
<meta charset="utf-8">
<title>Swift Haul Away – Rubbish Removal</title>
<link rel="stylesheet" href="https://fonts.googleapis.com/css2?family=Montserrat:wght@600;700;800&family=Lato:wght@400;700&display=swap">
<style>
:root{
  --lime:#a4bd13;
  --lime-dark:#8fa80c;
  --blue:#1a64ad;
  --blue-dark:#0f4f94;
  --ink:#262626;
  --muted:#6f6f6f;
  --card:#ececec;
  --white:#ffffff;
  --head:"Montserrat",sans-serif;
  --body:"Lato",sans-serif;
}
*{box-sizing:border-box;margin:0;padding:0}
html,body{width:1200px;height:4728px;overflow:hidden}
body{position:relative;font-family:var(--body);color:var(--ink);background:var(--white)}
section,header,footer{position:absolute;left:0;width:1200px}
.abs{position:absolute}
.btn{position:absolute;display:flex;align-items:center;justify-content:center;background:var(--lime);color:var(--white);font-family:var(--body);font-weight:700;font-size:12px;border-radius:26px;letter-spacing:.2px}
.rule{position:absolute;height:3px;width:55px;background:var(--lime);left:572px}
.h2{position:absolute;left:0;width:1200px;text-align:center;font-family:var(--head);font-weight:700;color:var(--ink)}

/* header */
.site-header{top:0;height:143px;background:var(--white)}
.brand{left:110px;top:34px;display:flex;align-items:center;gap:12px}
.brand-mark{width:40px;height:40px;border-radius:50%;background:var(--lime)}
.brand-name{font-family:var(--head);font-weight:800;font-size:25px;color:var(--blue)}
.topbar{left:486px;top:0;width:602px;height:64px;background:var(--lime)}
.social{position:absolute;top:18px;width:28px;height:28px;border-radius:50%;background:rgba(255,255,255,.85)}
.call{position:absolute;left:258px;top:16px;display:flex;align-items:center;gap:10px;color:var(--white);font-size:12px;font-weight:700}
.call strong{font-size:19px}
.call-icon{width:34px;height:34px;border:2px solid var(--white);border-radius:50%;display:flex;align-items:center;justify-content:center}
.nav{left:453px;top:97px;display:flex;gap:28px;font-size:12px;font-weight:700;font-family:var(--body)}
.nav a{color:var(--ink);text-decoration:none}
.nav a.active{color:var(--lime);border-bottom:2px solid var(--lime);padding-bottom:6px}

/* hero */
.hero{top:143px;height:600px;background:linear-gradient(180deg,#1f56a8 0%,#2262b4 50%,#143f85 100%)}
.hero-photo{left:0;top:0;width:1200px;height:600px;background:linear-gradient(160deg,rgba(60,110,190,.55),rgba(20,60,140,.3))}
.hero h1{position:absolute;left:114px;top:220px;font-family:var(--head);font-weight:800;font-size:58px;line-height:62px;color:var(--white)}
.hero-art{left:716px;top:25px;width:330px;height:575px;border-radius:40px 40px 0 0;background:linear-gradient(180deg,rgba(163,189,19,.45),rgba(30,90,180,.35))}
.arrow{position:absolute;top:286px}
.scroll-down{left:576px;top:576px;width:48px;height:48px;border-radius:50%;background:var(--white);display:flex;align-items:center;justify-content:center;box-shadow:0 2px 6px rgba(0,0,0,.25)}

/* services split */
.services{top:743px;height:496px}
.svc{position:absolute;top:0;height:496px;width:600px;padding:90px 58px 0 110px;color:var(--white)}
.svc.res{left:0;background:var(--blue)}
.svc.com{left:600px;background:var(--lime);padding-left:68px;padding-right:100px}
.svc h3{font-family:var(--head);font-weight:700;font-size:21px;margin-bottom:24px}
.svc p{font-size:12.3px;line-height:21.5px;margin-bottom:21px;text-align:justify}
.services svg{position:absolute;left:0;top:0}

/* why */
.why{top:1239px;height:559px}
.feature{position:absolute;width:183px;height:183px;background:var(--card);border-radius:3px;text-align:center}
.feature .ico{position:absolute;left:58px;top:30px;width:66px;height:66px;border-radius:14px;background:linear-gradient(135deg,#cfe06a,#8fb7e3)}
.feature span{position:absolute;left:10px;right:10px;top:118px;font-size:14.5px;font-weight:700;line-height:21px}

/* property managers */
.property{top:1798px;height:477px}
.property-photo{left:0;top:0;width:1200px;height:477px;background:linear-gradient(90deg,#8c8c8c 0%,#bdbdbd 45%,#6f7880 70%,#a9b9cc 100%)}
.pm-box{left:119px;top:-33px;width:472px;height:422px;border:5px solid var(--white);background:linear-gradient(180deg,#8eb61a 0%,#3c9a56 55%,#1d6fa8 100%);color:var(--white);text-align:center;padding:48px 40px 0}
.pm-box h3{font-family:var(--head);font-weight:700;font-size:26px;line-height:31px}
.pm-box .line{width:55px;height:3px;background:var(--lime);margin:24px auto 34px;filter:brightness(1.15)}
.pm-box p{font-size:11.8px;line-height:16.6px;margin-bottom:16px}

/* quote */
.quote{top:2275px;height:755px}
.quote p{position:absolute;left:222px;width:756px;top:149px;text-align:center;font-size:12.3px;line-height:21px;color:var(--muted)}
.ba{position:absolute;top:323px;width:340px;height:338px;overflow:hidden}
.ba .half{position:absolute;top:0;width:170px;height:338px}
.ba .b{left:0;background:linear-gradient(180deg,#7a6a58,#4c4a48)}
.ba .a{left:170px;background:linear-gradient(180deg,#a6a19a,#6c6b69)}
.ba span{position:absolute;bottom:16px;color:var(--white);font-family:var(--head);font-weight:700;font-size:20px}

/* steps */
.steps{top:3030px;height:471px;background:var(--lime)}
.steps h2{position:absolute;left:110px;top:82px;font-family:var(--head);font-weight:800;font-size:34px;line-height:40px;color:var(--white)}
.step{position:absolute;top:192px;width:308px;height:193px;background:var(--white);border-radius:4px;box-shadow:0 3px 8px rgba(0,0,0,.2);padding:28px 32px}
.step .num{display:inline-flex;width:58px;height:58px;border-radius:50%;background:var(--blue);color:var(--white);align-items:center;justify-content:center;font-family:var(--head);font-weight:700;font-size:32px;vertical-align:middle}
.step b{font-family:var(--head);font-weight:600;font-size:20px;margin-left:12px;vertical-align:middle}
.step p{margin-top:24px;font-size:12.5px;line-height:21px;color:var(--muted)}

/* testimonials */
.testimonials{top:3501px;height:514px;background:#fafafa}
.tcard{position:absolute;top:169px;width:310px;height:244px;background:var(--white);border-bottom:4px solid var(--blue);box-shadow:0 2px 8px rgba(0,0,0,.1);padding:24px 30px}
.avatar{position:absolute;left:28px;top:22px;width:62px;height:62px;border-radius:50%;background:linear-gradient(135deg,#c9b8a8,#8a7a6c)}
.tcard .who{position:absolute;left:102px;top:32px}
.tcard .who b{display:block;font-size:14.5px;font-weight:700}
.tcard .who small{font-size:11.5px;color:var(--muted)}
.qmark{position:absolute;right:30px;top:24px;font-family:var(--head);font-weight:800;font-size:44px;color:var(--blue);line-height:1}
.tcard p{position:absolute;left:30px;right:26px;top:110px;font-style:italic;font-size:12px;line-height:22px;color:var(--muted)}

/* estimate */
.estimate{top:4015px;height:594px}
.estimate-photo{left:0;top:0;width:600px;height:594px;background:linear-gradient(160deg,#8aa1b5 0%,#d9823a 50%,#2d5fa6 100%)}
.estimate-form{left:600px;top:0;width:600px;height:594px;background:var(--lime)}
.estimate-form h3{position:absolute;left:53px;top:122px;font-family:var(--head);font-weight:700;font-size:23px;line-height:35px;color:var(--white)}
.field{position:absolute;height:52px;border:1.5px solid var(--white);color:var(--white);font-size:14px;padding:0 12px;display:flex;align-items:center;justify-content:space-between}
.submit{position:absolute;left:55px;top:453px;width:130px;height:52px;background:var(--blue-dark);color:var(--white);font-weight:700;font-size:14px;display:flex;align-items:center;justify-content:center}

/* footer */
.site-footer{top:4609px;height:119px;background:var(--blue);color:var(--white);font-size:12.5px}
.foot-links{position:absolute;left:112px;top:50px}
.foot-copy{position:absolute;right:110px;top:50px}
</style>
</head>
<body>

<header class="site-header">
  <div class="abs brand"><span class="brand-mark"></span><span class="brand-name">Swift Haul Away</span></div>
  <div class="abs topbar">
    <span class="social" style="left:16px"></span>
    <span class="social" style="left:56px"></span>
    <span class="social" style="left:96px"></span>
    <span class="social" style="left:136px"></span>
    <div class="call">
      <span class="call-icon"><svg width="16" height="16" viewBox="0 0 24 24"><path fill="#fff" d="M6.6 10.8a15 15 0 006.6 6.6l2.2-2.2c.3-.3.7-.4 1-.2 1.1.4 2.3.6 3.6.6.6 0 1 .4 1 1V20c0 .6-.4 1-1 1A17 17 0 013 4c0-.6.4-1 1-1h3.5c.6 0 1 .4 1 1 0 1.3.2 2.5.6 3.6.1.3 0 .7-.2 1z"/></svg></span>
      <span>Call us Today : <strong>+1 555 010 2030</strong></span>
    </div>
  </div>
  <nav class="abs nav">
    <a class="active" href="#">HOME</a><a href="#">AVAILABLE SERVICES</a><a href="#">EASY ONLINE QUOTES</a><a href="#">SERVICE AREAS</a><a href="#">FAQ</a><a href="#">CONTACT</a>
  </nav>
</header>

<section class="hero">
  <div class="abs hero-photo" role="img" aria-label="Suburban house and front lawn at dusk"></div>
  <h1>WE ARE RUBBISH<br>REMOVAL</h1>
  <a class="btn" style="left:114px;top:349px;width:163px;height:49px">GIVE US A CALL!</a>
  <div class="abs hero-art" role="img" aria-label="Cartoon superhero mascot carrying an armchair, TV, lamp and rubbish"></div>
  <svg class="arrow" style="left:46px" width="20" height="32" viewBox="0 0 20 32"><path d="M16 3 4 16l12 13" fill="none" stroke="#fff" stroke-width="3"/></svg>
  <svg class="arrow" style="left:1134px" width="20" height="32" viewBox="0 0 20 32"><path d="m4 3 12 13L4 29" fill="none" stroke="#fff" stroke-width="3"/></svg>
  <div class="abs scroll-down"><svg width="16" height="10" viewBox="0 0 16 10"><path d="m2 2 6 6 6-6" fill="none" stroke="#333" stroke-width="2"/></svg></div>
</section>

<section class="services">
  <div class="svc res">
    <h3>RESIDENTIAL SERVICES</h3>
    <p>We know how quickly unwanted items, junk &amp; debris can pile up inside and outside of your home. With our fast, reliable junk removal service we can get your space back to normal the same-day. Did you know? Most items we remove are re-homed, donated or recycled!</p>
    <p>If you want junk removed efficiently, by local friendly folk who arrive when they say they will and dispose of everything safely and responsibly for a competitive price, we're the team for you.</p>
  </div>
  <div class="svc com">
    <h3>COMMERCIAL SERVICES</h3>
    <p>Our commercial junk removal service includes the cleanup of offices, retail spaces, warehouses, storage units and any other commercial space that needs to be cleared of junk, trash and unwanted items.</p>
    <p>Whatever you want gone, we can handle. Our professional junk removal team can remove almost anything from your commercial property as long as it isn't a hazardous substance. Our team does full service junk removal, which means we do all the heavy lifting so you don't have to.</p>
  </div>
  <svg width="1200" height="496" viewBox="0 0 1200 496"><path d="M0 496Q600 310 1200 496Z" fill="#fff"/></svg>
</section>

<section class="why">
  <h2 class="h2" style="top:0;font-size:32px">WHY CHOOSE US?</h2>
  <div class="rule" style="top:53px"></div>
  <div class="feature" style="left:110px;top:86px"><div class="ico" role="img" aria-label="Clock and scale icon"></div><span>On Time, Every Time!</span></div>
  <div class="feature" style="left:308px;top:86px"><div class="ico" role="img" aria-label="Delivery cart icon"></div><span>Speedy Service</span></div>
  <div class="feature" style="left:508px;top:86px"><div class="ico" role="img" aria-label="Globe in hands icon"></div><span>Protecting the Environment</span></div>
  <div class="feature" style="left:706px;top:86px"><div class="ico" role="img" aria-label="Receipt icon"></div><span>No Hidden Fees</span></div>
  <div class="feature" style="left:905px;top:86px"><div class="ico" role="img" aria-label="Truck icon"></div><span>Big or Small We Take it All!</span></div>
  <div class="feature" style="left:211px;top:284px"><div class="ico" role="img" aria-label="Map pin globe icon"></div><span>Locally Owned</span></div>
  <div class="feature" style="left:409px;top:284px"><div class="ico" role="img" aria-label="Shield in hands icon"></div><span>Fully Insured</span></div>
  <div class="feature" style="left:607px;top:284px"><div class="ico" role="img" aria-label="Cleaning supplies icon"></div><span>Cleaning Up</span></div>
  <div class="feature" style="left:807px;top:284px"><div class="ico" role="img" aria-label="Online quote icon"></div><span>Easy Online Quotes</span></div>
</section>

<section class="property">
  <div class="abs property-photo" role="img" aria-label="Modern apartment building with balconies"></div>
  <div class="abs pm-box">
    <h3>PROPERTY MANAGERS<br>AND REALTORS</h3>
    <div class="line"></div>
    <p>We help property managers clear out clutter as well as take old furniture, appliances, trash and mattresses that tenants left behind or have dumped illegally on the property. This helps you get your units rented faster and keep your properties looking clean.</p>
    <p>Property Managers and Realtors rely on us to clear out properties that have been vacated and left in shambles by prior tenants. Our service allows for quick re-rental of the property and includes clearing out homes and apartments after evictions or messy tenants. We also compassionately help with hoarding situations and estate clean-outs.</p>
  </div>
</section>

<section class="quote">
  <h2 class="h2" style="top:68px;font-size:29px">GET YOUR EASY ONLINE QUOTE TODAY!</h2>
  <div class="rule" style="top:117px"></div>
  <p>We make it really easy for you to receive your junk removal quote. With the power of the internet there is no need to disrupt your busy schedule with an in-person quote. To get started simply click the link below and you will be taken to our online quote form. You will receive your junk removal quote quickly and hassle free.</p>
  <a class="btn" style="left:519px;top:224px;width:164px;height:48px">GIVE US A CALL!</a>
  <div class="ba" style="left:75px" role="img" aria-label="Garage before and after junk removal"><div class="half b"></div><div class="half a"></div><span style="left:30px">BEFORE</span><span style="left:214px">AFTER</span></div>
  <div class="ba" style="left:431px" role="img" aria-label="Storage room before and after junk removal"><div class="half b"></div><div class="half a"></div><span style="left:30px">BEFORE</span><span style="left:214px">AFTER</span></div>
  <div class="ba" style="left:785px" role="img" aria-label="Shed before and after junk removal"><div class="half b"></div><div class="half a"></div><span style="left:30px">BEFORE</span><span style="left:214px">AFTER</span></div>
</section>

<section class="steps">
  <h2>GETTING RID OF UNWANTED ITEMS, JUNK &amp; DEBRIS<br>IS AS EASY AS 1, 2, 3!</h2>
  <div class="step" style="left:114px"><span class="num">1</span><b>STEP 1</b><p>Use our easy online quote form to get your quote today!</p></div>
  <div class="step" style="left:446px"><span class="num">2</span><b>STEP 2</b><p>Schedule a day that works best for you. Same day, next day and after hour appointments are available.</p></div>
  <div class="step" style="left:780px"><span class="num">3</span><b>STEP 3</b><p>When our friendly, uniformed team arrives they make everything super simple for you! All you have to do is</p></div>
</section>

<section class="testimonials">
  <h2 class="h2" style="top:88px;font-size:33px">TESTIMONIALS</h2>
  <div class="tcard" style="left:110px"><div class="avatar" role="img" aria-label="Customer portrait"></div><div class="who"><b>John doe</b><small>Company name</small></div><span class="qmark">”</span><p>"Lorem ipsum dolor sit amet, consectetur adipiscing elit, sed do eiusmod tempor incididunt ut labore et dolore magna aliqua. Ut enim ad minim veniam, quis nostrud exercitation"</p></div>
  <div class="tcard" style="left:444px"><div class="avatar" role="img" aria-label="Customer portrait"></div><div class="who"><b>John doe</b><small>Company name</small></div><span class="qmark">”</span><p>"Lorem ipsum dolor sit amet, consectetur adipiscing elit, sed do eiusmod tempor incididunt ut labore et dolore magna aliqua. Ut enim ad minim veniam, quis nostrud exercitation"</p></div>
  <div class="tcard" style="left:778px"><div class="avatar" role="img" aria-label="Customer portrait"></div><div class="who"><b>John doe</b><small>Company name</small></div><span class="qmark">”</span><p>"Lorem ipsum dolor sit amet, consectetur adipiscing elit, sed do eiusmod tempor incididunt ut labore et dolore magna aliqua. Ut enim ad minim veniam, quis nostrud exercitation"</p></div>
</section>

<section class="estimate">
  <div class="abs estimate-photo" role="img" aria-label="Worker in orange high-visibility uniform beside blue wheelie bins"></div>
  <div class="abs estimate-form">
    <h3>SCHEDULE YOUR FREE<br>ESTIMATE</h3>
    <div class="field" style="left:55px;top:194px;width:241px">Name</div>
    <div class="field" style="left:301px;top:194px;width:244px">Email</div>
    <div class="field" style="left:55px;top:255px;width:241px">Phone</div>
    <div class="field" style="left:301px;top:255px;width:244px">City</div>
    <div class="field" style="left:55px;top:315px;width:490px">Address</div>
    <div class="field" style="left:55px;top:376px;width:490px">Residence type<svg width="10" height="6" viewBox="0 0 10 6"><path d="m1 1 4 4 4-4" fill="none" stroke="#fff" stroke-width="1.5"/></svg></div>
    <div class="submit">SUBMIT</div>
  </div>
</section>

<footer class="site-footer">
  <div class="foot-links">Home &nbsp;| &nbsp;Available Services &nbsp;| &nbsp;Easy Online Quotes &nbsp;| &nbsp;Service Areas &nbsp;| &nbsp;FAQ &nbsp;| &nbsp;Contact</div>
  <div class="foot-copy">© Copyrights 2021 Company name | All Rights Reserved</div>
</footer>

</body>
</html>
```